Design a building access mobile app for Quillo by Tamberlin Entry Systems

Hello, We're looking for an awesome designer to create an app design for our app Quillo, by Tamberlin Entry Systems. the mobile app allows employees open their office doors with their mobile phone. this means they don't have to use those plastic card badges or keys. We like clean modern design, dark and light themes. We don't have a logo yet.
Updates

Reason: Waiting on a couple designers to submit concepts

Target Market(s)

Commercial and employees

Industry/Entity Type

Building

Font styles to use
Sans Serif
Other font styles liked:
• Oswald extra light

Requirements
Must have
• nice clean design

```html
<!DOCTYPE html>
<html lang="en">
<head>
<meta charset="utf-8">
<title>Tamberlin Security – Door Access</title>
<link rel="stylesheet" href="https://fonts.googleapis.com/css2?family=Oswald:wght@200;300;400&family=Roboto:wght@500&display=swap">
<style>
  :root {
    --green-bright: #70ff12;
    --green-glow: #66f012;
    --green-button: #5fe40f;
    --green-ring: #68f212;
    --green-door: #56a81c;
    --green-label: #4f9a18;
    --green-version: #58c613;
    --white: #ffffff;
    --field-bg: #f1f1f1;
    --field-text: #c4c4c4;
    --pin-red: #ff1f3d;
  }
  * { margin: 0; padding: 0; box-sizing: border-box; }
  html, body { width: 675px; height: 1200px; overflow: hidden; }
  body { background: var(--green-bright); font-family: "Oswald", sans-serif; }

  .screen { position: relative; width: 675px; height: 1200px; overflow: hidden; background: var(--green-bright); }

  .backdrop {
    position: absolute; inset: 0;
    background: linear-gradient(160deg, #74ff1a 0%, #6cfb12 45%, #72ff16 100%);
  }

  .status-bar {
    position: absolute; top: 10px; left: 10px; right: 8px; height: 20px;
    display: flex; justify-content: space-between; align-items: center;
    color: var(--white); font-family: "Roboto", sans-serif; font-weight: 500; font-size: 14px;
  }
  .status-left, .status-right { display: flex; align-items: center; gap: 5px; width: 160px; }
  .status-right { justify-content: flex-end; }
  .status-time { position: absolute; left: 50%; transform: translateX(-50%); }

  .app-header { position: absolute; top: 50px; left: 0; right: 0; height: 48px; }
  .menu-button { position: absolute; left: 24px; top: 13px; }
  .app-title {
    position: absolute; left: 0; right: 0; top: 0; text-align: center;
    color: var(--white); font-weight: 300; font-size: 33px; line-height: 46px; letter-spacing: 0.2px;
  }
  .info-button { position: absolute; right: 22px; top: 10px; }

  .location-field {
    position: absolute; left: 50px; top: 174px; width: 576px; height: 72px;
    background: var(--field-bg); border-radius: 4px;
    box-shadow: 0 2px 4px rgba(0,0,0,0.08);
  }
  .location-placeholder {
    position: absolute; left: 24px; top: 0; line-height: 72px;
    color: var(--field-text); font-weight: 200; font-size: 29px;
  }
  .location-pin { position: absolute; right: 18px; top: 18px; }

  .door-control {
    position: absolute; left: 140px; top: 463px; width: 396px; height: 396px;
    border-radius: 50%; background: var(--green-ring);
    display: flex; align-items: center; justify-content: center;
  }
  .door-button {
    width: 358px; height: 358px; border-radius: 50%;
    background: linear-gradient(180deg, #62e810 0%, #5cdf0e 100%);
    box-shadow: 0 3px 6px rgba(60,140,10,0.35), inset 0 2px 2px rgba(255,255,255,0.08);
    display: flex; flex-direction: column; align-items: center; justify-content: center;
    padding-top: 10px;
  }
  .door-label {
    margin-top: 6px; color: var(--green-label);
    font-weight: 300; font-size: 40px; line-height: 54px;
  }

  .app-version {
    position: absolute; left: 0; right: 0; top: 1153px; text-align: center;
    color: var(--green-version); font-weight: 200; font-size: 24px;
  }
</style>
</head>
<body>
<main class="screen">
  <div class="backdrop" role="img" aria-label="Softly tinted photo of a bright office corridor with a doorway"></div>

  <div class="status-bar">
    <div class="status-left">
      <svg width="46" height="10" viewBox="0 0 46 10" fill="#fff" aria-hidden="true">
        <circle cx="5" cy="5" r="4.2"/><circle cx="14" cy="5" r="4.2"/><circle cx="23" cy="5" r="4.2"/><circle cx="32" cy="5" r="4.2"/><circle cx="41" cy="5" r="4.2"/>
      </svg>
      <svg width="16" height="12" viewBox="0 0 16 12" aria-hidden="true">
        <path d="M1 4 A10 10 0 0 1 15 4" stroke="#fff" stroke-width="1.8" fill="none"/>
        <path d="M3.8 7 A6 6 0 0 1 12.2 7" stroke="#fff" stroke-width="1.8" fill="none"/>
        <circle cx="8" cy="10" r="1.6" fill="#fff"/>
      </svg>
    </div>
    <span class="status-time">9:41 PM</span>
    <div class="status-right">
      <svg width="9" height="14" viewBox="0 0 9 14" aria-hidden="true">
        <path d="M1 4 L7 10 L4 13 V1 L7 4 L1 10" stroke="#fff" stroke-width="1.2" fill="none"/>
      </svg>
      <span>100%</span>
      <svg width="30" height="14" viewBox="0 0 30 14" aria-hidden="true">
        <rect x="0.75" y="0.75" width="26" height="12.5" rx="2.5" stroke="#fff" stroke-width="1.5" fill="none"/>
        <rect x="2.8" y="2.8" width="22" height="8.4" rx="1" fill="#fff"/>
        <rect x="27.8" y="4.5" width="2" height="5" rx="1" fill="#fff"/>
      </svg>
    </div>
  </div>

  <header class="app-header">
    <svg class="menu-button" width="31" height="20" viewBox="0 0 31 20" aria-label="Menu">
      <g stroke="#fff" stroke-width="2.2"><line x1="0" y1="1.5" x2="31" y2="1.5"/><line x1="0" y1="10" x2="31" y2="10"/><line x1="0" y1="18.5" x2="31" y2="18.5"/></g>
    </svg>
    <h1 class="app-title">Tamberlin Security</h1>
    <svg class="info-button" width="28" height="28" viewBox="0 0 28 28" aria-label="Information">
      <circle cx="14" cy="14" r="12.8" stroke="#fff" stroke-width="1.8" fill="none"/>
      <circle cx="14" cy="8.3" r="1.4" fill="#fff"/>
      <line x1="14" y1="11.5" x2="14" y2="20.5" stroke="#fff" stroke-width="1.8"/>
    </svg>
  </header>

  <div class="location-field">
    <span class="location-placeholder">Enter your office location</span>
    <svg class="location-pin" width="28" height="36" viewBox="0 0 28 36" aria-hidden="true">
      <path d="M14 35 C14 35 1.5 21 1.5 13 A12.5 12.5 0 0 1 26.5 13 C26.5 21 14 35 14 35 Z" fill="var(--pin-red)"/>
      <circle cx="14" cy="13" r="5" fill="#fff"/>
    </svg>
  </div>

  <div class="door-control">
    <div class="door-button">
      <svg class="door-icon" width="98" height="155" viewBox="0 0 98 155" aria-hidden="true">
        <path d="M4 129 V4 H94 V129" stroke="var(--green-door)" stroke-width="6" fill="none" stroke-linecap="round" stroke-linejoin="round"/>
        <path d="M52 36 L97 7 V129 L52 154 Z" fill="var(--green-door)"/>
        <circle cx="66" cy="93" r="4" fill="var(--green-button)"/>
        <line x1="59" y1="93" x2="66" y2="93" stroke="var(--green-button)" stroke-width="2"/>
      </svg>
      <span class="door-label">Door</span>
    </div>
  </div>

  <p class="app-version">v 2.0.1</p>
</main>
</body>
</html>
```